Facial Tissue Brand Logo and Design

We would like you to design a Logo for the Facial Tissue Brand "Velora" along with the box design. The pack should indicate the pack size (150 x 2 ply). Also our company logo should be present (attached) along with a barcode. The box size dimensions should be 210mm (L) x 110mm (W) x 70mm (H). We are open to all kinds of nice designs which are attractive but not overdone. Happy designing!

UPDATE:
We appreciate the designs so far... but would also love to see more options in a simple and elegent design style that would look good on a table... please see attached below links for reference purpose:

www.pictovault-example.com/image-photo/cleaning-wipes-isolated-on-white-257770819

www.pictovault-example.com/image-photo/cleaning-wipes-isolated-on-white-155326937

www.pictovault-example.com/image-photo/delicate-female-hands-pulling-tissue-out-1330426586

Happy desgining!

We appreciate the designs so far.. but would like to to see some more options.

```html
<!DOCTYPE html>
<html lang="en">
<head>
<meta charset="utf-8">
<title>Velora Facial Tissue – Box Dieline</title>
<link rel="stylesheet" href="https://fonts.googleapis.com/css2?family=Courgette&family=Montserrat:wght@300;600&display=swap">
<style>
  :root {
    --mint: #dff2ee;
    --mint-stripe: #c8e8e0;
    --mint-pale: #eaf7f4;
    --pink: #f9dde2;
    --teal: #119a87;
    --pink-accent: #e884ad;
    --navy: #24466e;
    --cut-line: #3a3a3a;
    --white: #ffffff;
    --page: #ffffff;
  }
  html, body {
    margin: 0;
    padding: 0;
    width: 1200px;
    height: 800px;
    overflow: hidden;
    background: var(--page);
  }
  .canvas {
    position: relative;
    width: 1200px;
    height: 800px;
    overflow: hidden;
    background: var(--page);
  }
  .dieline {
    position: absolute;
    left: 273px;
    top: 10px;
    width: 654px;
    height: 780px;
  }
  .base-fill { fill: url(#mint-stripes); }
  .pink-field { fill: var(--pink); stroke: var(--mint-pale); stroke-width: 50; stroke-linejoin: miter; }
  .cut-line { fill: none; stroke: var(--cut-line); stroke-width: 1.3; }
  .fold-line { stroke: var(--cut-line); stroke-width: 1; }
  .logo-plate { fill: var(--white); }
  .brand-name {
    font-family: "Courgette", cursive;
    fill: var(--teal);
    text-anchor: middle;
  }
  .brand-dot { fill: var(--pink-accent); }
  .product-line {
    font-family: "Courgette", cursive;
    fill: var(--pink-accent);
    text-anchor: middle;
  }
  .claim {
    font-family: "Courgette", cursive;
    font-size: 24px;
    fill: var(--teal);
  }
  .company-name {
    font-family: "Montserrat", sans-serif;
    font-weight: 300;
    font-size: 20px;
    fill: var(--navy);
  }
  .company-mark { fill: var(--navy); }
  .company-country {
    font-family: "Montserrat", sans-serif;
    font-weight: 300;
    font-size: 7px;
    fill: var(--navy);
  }
</style>
</head>
<body>
<main class="canvas">
  <svg class="dieline" viewBox="100 135 1090 1300" xmlns="http://www.w3.org/2000/svg" aria-label="Velora facial tissue box, flat dieline">
    <defs>
      <pattern id="mint-stripes" patternUnits="userSpaceOnUse" width="20" height="19">
        <rect width="20" height="19" fill="var(--mint)"/>
        <rect y="0" width="20" height="9" fill="var(--mint-stripe)"/>
      </pattern>
      <path id="outline-path" d="M282 142 L1050 142 L1115 165 L1115 360 L1050 383 L1005 383 L1005 395 L1170 400 L1180 410 L1180 742 L1170 748 L1005 755 L1005 762 L1050 762 L1115 780 L1115 985 L1050 1003 L1005 1003 L1040 1020 L1105 1040 L1105 1100 L1180 1105 L1180 1280 L1105 1285 L1105 1345 L1040 1370 L1005 1382 L988 1425 L298 1425 L282 1382 L245 1370 L180 1345 L180 1285 L105 1280 L105 1105 L180 1100 L180 1040 L245 1020 L282 1003 L235 1003 L170 985 L170 780 L235 762 L282 762 L282 755 L115 748 L105 740 L105 410 L115 400 L282 392 L282 383 L235 383 L170 360 L170 165 L235 142 Z"/>
      <clipPath id="box-shape">
        <use href="#outline-path"/>
      </clipPath>
      <clipPath id="upper-panels">
        <rect x="282" y="142" width="723" height="620"/>
        <rect x="1005" y="142" width="110" height="241"/>
      </clipPath>
      <clipPath id="lower-panels">
        <rect x="100" y="762" width="905" height="668"/>
      </clipPath>
    </defs>

    <g class="print-area" clip-path="url(#box-shape)">
      <rect class="base-fill" x="100" y="135" width="1090" height="1300"/>
      <g clip-path="url(#upper-panels)">
        <polygon class="pink-field" role="img" aria-label="Soft pink polka-dot pattern field"
          points="900,100 1200,100 1200,800 1050,800 630,383"/>
      </g>
      <g clip-path="url(#lower-panels)">
        <polygon class="pink-field" role="img" aria-label="Soft pink polka-dot pattern field"
          points="40,740 269,740 660,1140 346,1460 40,1460"/>
      </g>
    </g>

    <g class="fold-lines">
      <line class="fold-line" x1="282" y1="142" x2="282" y2="1382"/>
      <line class="fold-line" x1="1005" y1="142" x2="1005" y2="1382"/>
      <line class="fold-line" x1="282" y1="383" x2="1005" y2="383"/>
      <line class="fold-line" x1="282" y1="762" x2="1005" y2="762"/>
      <line class="fold-line" x1="282" y1="1003" x2="1005" y2="1003"/>
      <line class="fold-line" x1="282" y1="1382" x2="1005" y2="1382"/>
    </g>
    <use href="#outline-path" class="cut-line"/>

    <g class="brand-lockup" transform="rotate(180 645 255)">
      <ellipse class="logo-plate" cx="645" cy="255" rx="140" ry="62"/>
      <text class="brand-name" x="638" y="270" font-size="54">Velora</text>
      <circle class="brand-dot" cx="738" cy="236" r="8"/>
      <text class="product-line" x="645" y="298" font-size="15">Facial Tissue</text>
    </g>

    <g class="brand-lockup">
      <ellipse class="logo-plate" cx="643" cy="572" rx="200" ry="90"/>
      <text class="brand-name" x="633" y="590" font-size="80">Velora</text>
      <circle class="brand-dot" cx="780" cy="540" r="11"/>
      <text class="product-line" x="700" y="628" font-size="20">Facial Tissue</text>
    </g>
    <text class="claim" x="310" y="735">100 % Pure Hygenic</text>
    <text class="claim" x="815" y="738">100 Sheets</text>

    <g class="brand-lockup">
      <ellipse class="logo-plate" cx="647" cy="880" rx="140" ry="62"/>
      <text class="brand-name" x="640" y="895" font-size="54">Velora</text>
      <circle class="brand-dot" cx="740" cy="860" r="8"/>
      <text class="product-line" x="695" y="922" font-size="15">Facial Tissue</text>
    </g>

    <g class="company-block" transform="translate(215 445) rotate(90)">
      <rect class="company-mark" x="0" y="-10" width="28" height="28"/>
      <text class="company-name" x="40" y="10" textLength="220" lengthAdjust="spacingAndGlyphs">NORWEN TRADING FZC</text>
      <text class="company-country" x="0" y="65" textLength="260" lengthAdjust="spacing">UNITED ARAB EMIRATES</text>
    </g>

    <g class="company-block" transform="translate(1080 705) rotate(-90)">
      <rect class="company-mark" x="0" y="-10" width="28" height="28"/>
      <text class="company-name" x="40" y="10" textLength="220" lengthAdjust="spacingAndGlyphs">NORWEN TRADING FZC</text>
      <text class="company-country" x="0" y="62" textLength="260" lengthAdjust="spacing">UNITED ARAB EMIRATES</text>
    </g>
  </svg>
</main>
</body>
</html>
```